High-Converting Facebook Ads for Portals Drapes & Louvres (6 Products)

We are looking for a graphic designer to create high-quality Facebook & Instagram ads for our business: Portals Drapes and Louvres (Melbourne, Australia).

We require 6 separate ad designs, each for a different product:

Zipscreen Blinds

Outdoor Awnings

Plantation Shutters

Roller Shutters

Security Doors

Roller Blinds & Sheer Curtains

Ad Specifications:

Sizes:

1440 x 1800 px (4:5 ratio)

1080 x 1080 px (1:1 ratio)

1080 x 1920 px (9:16 ratio for Stories/Reels)

Format: PNG (high resolution, not blurry)

Designed specifically for Meta (Facebook/Instagram ads)

Mobile-friendly layout (clear, easy to read)

Style:

Bold, sales-driven, retail-style ads (NOT minimal)

Eye-catching and designed to generate leads

Clean, professional layout

Similar to promotional home improvement ads

Brand Colours:

Red: #E31E24

Blue: #0072BC

White backgrounds

Each ad must include:

“SALE NOW ON” banner at top

Our showroom address:
482 Upper Wattleby Road, Kestrel Heights (must be fully visible, not cut off)

Phone number: 9471 2658

Our logo (provided)

Badge: “Celebrating 13 YEARS in Business” (must be clean and readable)

Call to Action:

For 5 ads: “Book a FREE quote TODAY!”

For Security Doors ad: “ORDER NOW”

Offers / Pricing:

Most products: “UP TO 40% OFF”

Plantation Shutters: “FROM $299/sqm”

Security Doors: “FROM $750”

Content for each ad (examples):

Zipscreen Blinds:

Made to Measure

Fully Installed

Wind, Sun & Insect Protection

Outdoor Awnings:

Reduce Heat & Glare

Energy Saving

Custom Made

Plantation Shutters:

Modern & Elegant

Light & Privacy Control

Durable & Easy Care

Roller Shutters:

Security Protection

Block Heat & Noise

Total Light Control

Security Doors:

3 Point Locking

Premium Mesh

Custom Made

Blinds & Sheers:

Huge Range of Fabrics

Modern Soft Finish

Perfect for Any Room

Important Notes:

All text must be sharp and easy to read (no blur)

Layout must be balanced and not overcrowded

Ensure no text is cut off (especially address and headings)

Badge text must be straight and professional (no distortion)

Use high-quality, relevant images (we will provide references)

Goal:
Create ads that look professional, trustworthy, and generate enquiries/bookings for in-home quotes.

We are open to creative ideas but want a strong, bold retail-style ad that converts.
I have uploaed chatgpt mocks

Target Market(s)

Homeowners in Melbourne, Australia (typically aged 30–65) looking to improve their homes with blinds, shutters, awnings and security doors. Mid to high income households focused on quality, security, and modern home upgrades.

Industry/Entity Type

Home Improvement / Construction / Retail

Font styles to use
Sans Serif

Requirements
Must have
• Clear, bold and easy-to-read text (must be readable on mobile) High-quality, non-blurry design Strong “SALE” style layout (retail promotional look) Proper spacing (no overcrowded designs) All key info visible (address must NOT be cut off) Correct pricing and offers included Clean “13 YEARS” badge (no distortion or curved text) Consistent branding across all 6 ads
Nice to have
• Modern, slightly premium feel while still being bold Good use of contrast (red/blue/white) Subtle shadows or layering to improve depth Clean use of icons or bullet points Strong hierarchy (headline → benefits → offer → CTA) Variations in layout for testing different ad styles
Should not have
• Minimal or plain designs (we want bold, sales-driven ads) Hard-to-read fonts or script fonts Low-quality or blurry images Overcrowded layouts with too much text Important text cut off (especially address or headings) Overuse of effects or “cheap” looking graphics Yellow-heavy colour schemes (must follow brand colours)

```html
<!DOCTYPE html>
<html lang="en">
<head>
<meta charset="utf-8">
<title>Portals Drapes &amp; Louvres – Blinds &amp; Sheers Sale</title>
<link rel="stylesheet" href="https://fonts.googleapis.com/css2?family=Montserrat:wght@800;900&family=Oswald:wght@600;700&family=Roboto:wght@500;700&display=swap">
<style>
  :root{
    --red:#e31e24;
    --blue:#0072bc;
    --blue-deep:#0a4f9c;
    --white:#ffffff;
    --ink:#111111;
    --gold:#d9a21b;
    --gold-light:#f4cb4a;
    --badge-dark:#1b1b1b;
    --rule:#cfcfcf;
  }
  *{margin:0;padding:0;box-sizing:border-box}
  html,body{width:675px;height:1200px;overflow:hidden;background:var(--white)}
  .ad{position:relative;width:675px;height:1200px;overflow:hidden;background:var(--white);font-family:"Roboto",sans-serif}

  .sale-banner{position:absolute;left:0;top:0;width:675px;height:314px;background:var(--red);color:var(--white);font-family:"Montserrat",sans-serif;font-weight:900;text-align:center}
  .sale-banner .sale{position:absolute;left:0;right:0;top:2px;font-size:218px;line-height:1;letter-spacing:-4px;transform:scaleX(0.86);transform-origin:center}
  .sale-banner .now-on{position:absolute;left:0;right:0;top:186px;font-size:120px;line-height:1;letter-spacing:-3px;transform:scaleX(0.93);transform-origin:center}

  .product-band{position:absolute;left:0;top:320px;width:675px;height:94px;background:linear-gradient(90deg,var(--blue) 0%,var(--blue-deep) 100%)}
  .product-band .title{position:absolute;left:41px;top:2px;font-family:"Oswald",sans-serif;font-weight:700;font-size:60px;line-height:1.15;color:var(--white);letter-spacing:0.5px}
  .product-band .url{position:absolute;left:42px;top:67px;font-size:15px;letter-spacing:3.1px;color:var(--white);font-weight:500}

  .years-badge{position:absolute;left:470px;top:302px;width:164px;height:164px}

  .features{position:absolute;left:41px;top:432px;width:189px;text-align:center}
  .feature{height:154px;border-bottom:1.5px solid var(--rule)}
  .feature:last-child{border-bottom:none}
  .feature .icon{display:block;margin:0 auto;width:82px;height:82px}
  .feature .label{margin-top:6px;font-size:20px;font-weight:500;line-height:1.2;color:var(--ink)}

  .offer{position:absolute;left:26px;top:902px;width:220px;height:100px}
  .offer .up-to{position:absolute;left:-26px;top:34px;width:92px;transform:rotate(-90deg);font-family:"Montserrat",sans-serif;font-weight:900;font-size:25px;color:var(--blue);text-align:center;line-height:1}
  .offer .amount{position:absolute;left:32px;top:-14px;font-family:"Oswald",sans-serif;font-weight:700;font-size:112px;line-height:1;color:var(--red);letter-spacing:-3px}
  .offer .pct{position:absolute;left:152px;top:-6px;font-family:"Montserrat",sans-serif;font-weight:900;font-size:64px;line-height:1;color:var(--red)}
  .offer .off{position:absolute;left:152px;top:52px;font-family:"Oswald",sans-serif;font-weight:700;font-size:46px;line-height:1;color:var(--red)}

  .photo-frame{position:absolute;left:268px;top:426px;width:407px;height:582px;background:var(--blue)}
  .photo-frame .inner{position:absolute;left:26px;top:26px;right:0;bottom:0;background:var(--white)}
  .photo{position:absolute;left:37px;top:35px;right:0;bottom:0;background:linear-gradient(180deg,#e4e2df 0%,#c9c4bc 30%,#a8a095 60%,#8b7258 100%)}

  .brand-block{position:absolute;left:0;top:1020px;width:268px;height:180px;background:linear-gradient(135deg,#f4f4f4 0%,#e2e2e2 100%);display:flex;align-items:center;justify-content:center;gap:8px}
  .brand-block .mark{width:14px;height:14px;background:var(--red)}
  .brand-block .name{font-family:"Roboto",sans-serif;font-weight:700;font-size:19px;color:var(--blue);line-height:1.2}

  .contact{position:absolute;left:268px;top:1020px;width:407px;height:180px;background:var(--red)}
  .contact .cta{position:absolute;left:9px;top:10px;right:0;height:53px;background:var(--blue);color:var(--white);font-family:"Montserrat",sans-serif;font-weight:800;font-size:23px;display:flex;align-items:center;justify-content:center;letter-spacing:-0.3px}
  .contact .phone{position:absolute;left:9px;top:63px;right:0;height:68px;display:flex;align-items:center;justify-content:center;gap:18px;color:var(--white);font-family:"Roboto",sans-serif;font-weight:700;font-size:46px;letter-spacing:1px}
  .contact .phone svg{width:40px;height:40px}
  .contact .address{position:absolute;left:9px;top:131px;right:0;bottom:0;background:var(--blue);color:var(--white);font-family:"Roboto",sans-serif;font-weight:700;font-size:14.5px;display:flex;align-items:center;justify-content:center;gap:6px}
  .contact .address svg{width:12px;height:12px}
</style>
</head>
<body>
<div class="ad">

  <header class="sale-banner">
    <div class="sale">SALE</div>
    <div class="now-on">NOW ON</div>
  </header>

  <section class="product-band">
    <div class="title">Blinds &amp; Sheers</div>
    <div class="url">www.portalsdrapesandlouvres.com.au</div>
  </section>

  <section class="photo-frame">
    <div class="inner"></div>
    <div class="photo" role="img" aria-label="Living room with sheer curtains across glass doors, white sofa and timber table"></div>
  </section>

  <svg class="years-badge" viewBox="0 0 164 164" aria-label="Celebrating 13 years in business">
    <circle cx="82" cy="82" r="81" fill="var(--gold)"/>
    <circle cx="82" cy="82" r="75" fill="var(--gold-light)"/>
    <circle cx="82" cy="82" r="46" fill="var(--badge-dark)"/>
    <circle cx="82" cy="82" r="46" fill="none" stroke="var(--gold)" stroke-width="2"/>
    <text x="82" y="31" text-anchor="middle" font-family="Montserrat,sans-serif" font-weight="900" font-size="10" letter-spacing="0.5" fill="var(--badge-dark)">CELEBRATING</text>
    <text x="82" y="66" text-anchor="middle" font-size="9" fill="var(--gold-light)">★ ★ ★</text>
    <text x="82" y="91" text-anchor="middle" font-family="Oswald,sans-serif" font-weight="700" font-size="22" fill="var(--white)">13 YEARS</text>
    <text x="82" y="108" text-anchor="middle" font-size="9" fill="var(--gold-light)">★ ★ ★</text>
    <text x="82" y="142" text-anchor="middle" font-family="Montserrat,sans-serif" font-weight="900" font-size="10" letter-spacing="0.5" fill="var(--badge-dark)">IN BUSINESS</text>
  </svg>

  <section class="features">
    <div class="feature">
      <svg class="icon" viewBox="0 0 82 82">
        <circle cx="41" cy="41" r="39" fill="var(--red)"/>
        <circle cx="41" cy="41" r="35" fill="var(--white)"/>
        <circle cx="41" cy="41" r="32" fill="var(--blue)"/>
        <path d="M41 24 L60 33 L41 42 L22 33 Z" fill="var(--white)"/>
        <path d="M24 40 L41 48 L58 40 L60 41 L41 50 L22 41 Z" fill="var(--white)"/>
        <path d="M24 47 L41 55 L58 47 L60 48 L41 57 L22 48 Z" fill="var(--white)"/>
      </svg>
      <div class="label">Huge Range<br>of Fabrics</div>
    </div>
    <div class="feature">
      <svg class="icon" viewBox="0 0 82 82">
        <circle cx="41" cy="41" r="39" fill="var(--red)"/>
        <circle cx="41" cy="41" r="35" fill="var(--white)"/>
        <circle cx="41" cy="41" r="32" fill="var(--blue)"/>
        <path d="M58 24 C44 24 30 34 28 50 L26 58 L29 58 L32 51 C46 50 56 38 58 24 Z" fill="var(--white)"/>
      </svg>
      <div class="label">Modern<br>Soft Finish</div>
    </div>
    <div class="feature">
      <svg class="icon" viewBox="0 0 82 82">
        <circle cx="41" cy="41" r="39" fill="var(--red)"/>
        <circle cx="41" cy="41" r="35" fill="var(--white)"/>
        <circle cx="41" cy="41" r="32" fill="var(--blue)"/>
        <path d="M24 30 L41 24 L58 30 L58 54 L41 60 L24 54 Z" fill="var(--white)"/>
        <rect x="29" y="36" width="9" height="8" fill="var(--blue)"/>
        <rect x="44" y="38" width="9" height="16" fill="var(--blue)"/>
      </svg>
      <div class="label">Perfect for<br>Any Room</div>
    </div>
  </section>

  <section class="offer">
    <div class="up-to">UP TO</div>
    <div class="amount">40</div>
    <div class="pct">%</div>
    <div class="off">OFF</div>
  </section>

  <section class="brand-block">
    <span class="mark"></span>
    <span class="name">Portals Drapes<br>&amp; Louvres</span>
  </section>

  <section class="contact">
    <div class="cta">Book a FREE quote TODAY!</div>
    <div class="phone">
      <svg viewBox="0 0 40 40">
        <circle cx="20" cy="20" r="20" fill="var(--white)"/>
        <path d="M13 10 L17 10 L19 16 L16 18 C17 21 19 23 22 24 L24 21 L30 23 L30 27 C30 29 28 30 26 30 C17 29 11 23 10 14 C10 12 11 10 13 10 Z" fill="var(--red)"/>
      </svg>
      <span>9471 2658</span>
    </div>
    <div class="address">
      <svg viewBox="0 0 12 12"><path d="M6 1 C8.2 1 9.5 2.6 9.5 4.5 C9.5 7 6 11 6 11 C6 11 2.5 7 2.5 4.5 C2.5 2.6 3.8 1 6 1 Z" fill="none" stroke="var(--white)" stroke-width="1.3"/><circle cx="6" cy="4.5" r="1.2" fill="var(--white)"/></svg>
      <span>482 Upper Wattleby Road, Kestrel Heights</span>
    </div>
  </section>

</div>
</body>
</html>
```